Need a developer to develop and design my virtual employee recruitment solution website.

I need the entire website developed, from the design, the navigation, the contents of the website, etc. I need a professional looking website yet have that modern look. You can suggest the best fonts, color combinations to use. I need the site to be SEO friendly. I also want high quality stock photos to be used on the website. I wanted to achieve a similar website like this https://remotehelperpool.example/.

Target Market(s)

Ecommerce Entrepreneurs, Businessmen, Cartwell and Bazorra Sellers.

Industry/Entity Type

Professional Service

Coding

Coded - Design and coding required

Number of Pages Required

5+ page

Font styles to use
Sans Serif

Requirements
Must have
• I wanted it to have pages like this https://remotehelperpool.example/
Nice to have
• open for any recommendation you can suggest
Should not have
• Cannot think of any. You can suggest your own here

```html
<!DOCTYPE html>
<html lang="en">
<head>
<meta charset="utf-8">
<title>HarborStaff – Virtual Employee Recruitment Agency</title>
<link href="https://fonts.googleapis.com/css2?family=Rubik:wght@400;500;700;800&family=Roboto:wght@400;500&display=swap" rel="stylesheet">
<style>
:root{
  --blue:#1465c7;
  --ink:#1b1b1b;
  --text:#3c3c3c;
  --muted:#5a5a5a;
  --pale:#e3eefa;
  --line:#c9d6e6;
  --footer:#1d1d1d;
  --white:#ffffff;
}
*{box-sizing:border-box;margin:0;padding:0}
html,body{width:1200px;height:5324px;overflow:hidden;background:var(--white)}
body{position:relative;font-family:"Roboto",Arial,sans-serif;color:var(--text)}
h1,h2,h3,.nav,.btn,.card-label,.card-num{font-family:"Rubik",Arial,sans-serif}
.abs{position:absolute}

/* header + hero */
.hero{position:absolute;left:0;top:0;width:1200px;height:660px;overflow:hidden}
.hero-photo{position:absolute;inset:0;background:linear-gradient(180deg,#d9c7bd 0%,#b7b6bd 35%,#6f8797 60%,#6d7f86 78%,#8c8378 100%)}
.hero-curve{position:absolute;left:0;top:540px}
.logo{position:absolute;left:110px;top:22px;display:flex;align-items:center;gap:12px;height:100px}
.logo-mark{width:30px;height:30px;border-radius:50%;background:var(--blue)}
.logo-name{font-family:"Rubik",sans-serif;font-weight:700;font-size:26px;color:var(--blue)}
.nav{position:absolute;left:310px;top:64px;display:flex;gap:31px;font-size:14px;color:#2a2a2a;letter-spacing:.2px}
.nav .active{color:var(--blue);font-weight:500}
.hero-title{position:absolute;left:550px;top:230px;font-size:36px;font-weight:700;line-height:42px;color:var(--ink)}
.hero-title span{color:var(--blue)}
.btn{position:absolute;left:554px;top:339px;width:164px;height:37px;border-radius:19px;background:var(--blue);color:#fff;font-size:15px;font-weight:500;display:flex;align-items:center;justify-content:center}
.hero-chevron{position:absolute;left:592px;top:492px}

/* welcome */
.section-title{font-size:34px;font-weight:700;line-height:42px;color:var(--ink)}
.section-title span{color:var(--blue)}
.welcome-title{left:112px;top:710px}
.welcome-copy{left:110px;top:812px;width:480px;font-size:13px;line-height:25px}
.welcome-copy p+p{margin-top:25px}
.perks{left:647px;top:770px;width:460px}
.perks h3{font-size:16px;font-weight:700;color:var(--ink);margin-bottom:24px}
.perks li{list-style:none;font-size:13px;line-height:31px;padding-left:30px;position:relative}
.perks li::before{content:"";position:absolute;left:0;top:9px;width:13px;height:13px;border-radius:50%;background:var(--blue)}
.perks li::after{content:"";position:absolute;left:4px;top:12px;width:3px;height:5px;border:solid #fff;border-width:0 2px 2px 0;transform:rotate(45deg)}

/* who */
.who-photo{left:170px;top:1178px;width:340px;height:340px;border-radius:50%;background:linear-gradient(135deg,#bfe3ef 0%,#5aa3a0 50%,#d9d2c2 100%)}
.who-title{left:645px;top:1116px}
.who-copy{left:645px;top:1222px;width:440px;font-size:13px;line-height:26px}
.who-copy strong{color:var(--ink)}
.who-copy p+p{margin-top:26px}

/* why */
.why-title{left:0;top:1658px;width:1200px;text-align:center}
.timeline-line{left:589px;top:1950px;width:1px;height:2880px;background:var(--line)}
.dot{position:absolute;width:18px;height:18px;border-radius:50%;border:1.5px solid #6f9ad0;background:#fff}
.connector{position:absolute;height:1px;background:var(--line)}
.perk-text{position:absolute;width:300px;font-size:16px;line-height:26px;color:var(--muted)}
.perk-icon{display:block;margin-bottom:18px}
.card{position:absolute;width:440px;height:280px}
.card-box{position:absolute;top:62px;height:160px;background:var(--pale)}
.card.right .card-box{left:80px;width:330px}
.card.left .card-box{left:56px;width:310px}
.card-label{position:absolute;top:140px;transform:translateY(-50%);font-size:26px;font-weight:700;line-height:33px;color:var(--ink);white-space:nowrap}
.card-num{position:absolute;top:140px;transform:translateY(-50%);font-size:58px;font-weight:800;color:var(--ink);line-height:1}
.card.right .card-num{left:302px}
.card.left .card-num{left:83px}

/* footer */
.footer{position:absolute;left:0;top:5060px;width:1200px;height:264px;background:var(--footer);color:#fff}
.footer-nav{position:absolute;left:0;top:80px;width:1200px;display:flex;justify-content:center;gap:30px;font-size:14px;color:#e4e4e4}
.footer-nav .active{font-weight:500;color:#fff}
.social{position:absolute;left:548px;top:148px;display:flex;gap:26px}
.social span{width:14px;height:14px;border-radius:50%;background:#fff}
.copyright{position:absolute;left:0;top:205px;width:1200px;text-align:center;font-size:11px;color:#ddd}
</style>
</head>
<body>

<header class="hero">
  <div class="hero-photo" role="img" aria-label="Photo of a man working on a laptop while sitting on a pebble beach by the sea at sunset"></div>
  <svg class="hero-curve" width="1200" height="120" viewBox="0 0 1200 120">
    <path d="M0 20 C 300 110, 700 120, 1200 25 L1200 120 L0 120 Z" fill="#fff"/>
    <path d="M0 20 C 300 110, 700 120, 1200 25" fill="none" stroke="var(--blue)" stroke-width="10"/>
  </svg>
  <div class="logo"><span class="logo-mark"></span><span class="logo-name">HARBORSTAFF</span></div>
  <nav class="nav">
    <span class="active">HOME</span><span>ABOUT US</span><span>SERVICES OFFERED</span><span>PRICING</span><span>TESTIMONIALS</span><span>FAQS</span><span>CONTACT US</span><span>BLOG</span>
  </nav>
  <h1 class="hero-title">WE ARE A <span>VIRTUAL EMPLOYEE</span><br><span>RECRUITMENT</span> AGENCY.</h1>
  <a class="btn">Register Now</a>
  <svg class="hero-chevron" width="16" height="10" viewBox="0 0 16 10"><path d="M2 2 L8 8 L14 2" fill="none" stroke="#fff" stroke-width="2"/></svg>
</header>

<section>
  <h2 class="section-title abs welcome-title">WELCOME TO<br><span>HARBORSTAFF</span></h2>
  <div class="abs welcome-copy">
    <p>Tired of being stuck in your 9-5 cubicle job? Exhausted from commuting to and from the office? Want to spend more time with your family? We've got you covered.</p>
    <p>HarborStaff is a virtual staffing company that helps freelancers and virtual assistants find their perfect work-from-home job. We have a pool of clients from all over the world who are all looking for talented virtual assistants.</p>
  </div>
  <div class="abs perks">
    <h3>With HarborStaff, you get to</h3>
    <ul>
      <li>Work from the comfort of your home</li>
      <li>Have a competitive and steady income</li>
      <li>Achieve work-life balance</li>
      <li>Learn new skills for free</li>
      <li>Work with a dedicated team who can provide you with HR, payroll, IT, and training assistance 24/7!</li>
    </ul>
  </div>
</section>

<section>
  <div class="abs who-photo" role="img" aria-label="Photo of a virtual assistant working on a laptop on a tropical beach"></div>
  <h2 class="section-title abs who-title">WHO ARE OUR<br><span>VIRTUAL ASSISTANTS?</span></h2>
  <div class="abs who-copy">
    <p><strong>We have VAs from all over the Philippines.</strong><br>Our VA pool is composed of highly dedicated people armed with the right set of skills clients are looking for in a virtual assistant. We hire VAs of varying work experience and skill levels, and we help our VAs improve their skills so that they can get the jobs and clients they want.</p>
    <p>HarborStaff accepts VAs in a variety of niches. Currently, our VAs belongs to one or more of the following groups: Administrative VAs, eCommerce VAs, and Specialist VAs.<br>Are you ready to join the team? To start the application process, please click on the button below.</p>
  </div>
</section>

<section>
  <h2 class="section-title abs why-title">WHY WORK FOR <span>HARBORSTAFF?</span></h2>
  <div class="abs timeline-line"></div>

  <!-- 01 -->
  <div class="perk-text" style="left:190px;top:1826px"><svg class="perk-icon" width="42" height="42" viewBox="0 0 42 42"><circle cx="22" cy="21" r="16" fill="none" stroke="var(--blue)" stroke-width="4"/><path d="M22 12 V21 L28 25" fill="none" stroke="var(--blue)" stroke-width="4"/></svg>We offer competitive rates based on your years of experience and skill proficiency.</div>
  <span class="dot" style="left:520px;top:1943px"></span><span class="connector" style="left:538px;top:1952px;width:51px"></span>
  <div class="card right" style="left:630px;top:1780px"><div class="card-box"></div><span class="card-label" style="left:44px">COMPETITIVE<br>HOURLY RATES</span><span class="card-num">01</span></div>

  <!-- 02 -->
  <div class="card left" style="left:130px;top:2070px"><div class="card-box"></div><span class="card-num">02</span><span class="card-label" style="left:196px">FLEXIBLE<br>HOURS</span></div>
  <span class="dot" style="left:637px;top:2213px"></span><span class="connector" style="left:590px;top:2222px;width:47px"></span>
  <div class="perk-text" style="left:690px;top:2130px"><svg class="perk-icon" width="42" height="42" viewBox="0 0 42 42"><circle cx="21" cy="21" r="17" fill="none" stroke="var(--blue)" stroke-width="4"/><path d="M21 11 V21 L27 25" fill="none" stroke="var(--blue)" stroke-width="4"/></svg>Full-time or part-time? We'll match you with a client whose staffing needs perfectly matches your availability!</div>

  <!-- 03 -->
  <div class="perk-text" style="left:190px;top:2392px"><svg class="perk-icon" width="42" height="42" viewBox="0 0 42 42"><rect x="4" y="8" width="34" height="30" rx="3" fill="none" stroke="var(--blue)" stroke-width="4"/><rect x="4" y="8" width="34" height="9" fill="var(--blue)"/><path d="M12 3 V11 M30 3 V11" stroke="var(--blue)" stroke-width="4"/></svg>We have clients from different time zones all over the world. We'll help you find the best fit for your schedule.</div>
  <span class="dot" style="left:520px;top:2511px"></span><span class="connector" style="left:538px;top:2520px;width:51px"></span>
  <div class="card right" style="left:630px;top:2348px"><div class="card-box"></div><span class="card-label" style="left:95px">FLEXIBLE<br>SCHEDULE</span><span class="card-num">03</span></div>

  <!-- 04 -->
  <div class="card left" style="left:130px;top:2637px"><div class="card-box"></div><span class="card-num">04</span><span class="card-label" style="left:184px">WEEKLY PAYOUT<br>VIA PAYLOOP</span></div>
  <span class="dot" style="left:637px;top:2780px"></span><span class="connector" style="left:590px;top:2789px;width:47px"></span>
  <div class="perk-text" style="left:690px;top:2698px"><svg class="perk-icon" width="42" height="42" viewBox="0 0 42 42"><circle cx="17" cy="21" r="14" fill="var(--blue)"/></svg>Your work is billed by the hour, and we will pay your client-verified hours each week.</div>

  <!-- 05 -->
  <div class="perk-text" style="left:190px;top:2960px"><svg class="perk-icon" width="42" height="42" viewBox="0 0 42 42"><circle cx="17" cy="21" r="14" fill="var(--blue)"/></svg>Here at RoundClockVA, we shoulder the PayLoop fees. We want you to get your hard-earned money in full!</div>
  <span class="dot" style="left:520px;top:3078px"></span><span class="connector" style="left:538px;top:3087px;width:51px"></span>
  <div class="card right" style="left:630px;top:2916px"><div class="card-box"></div><span class="card-label" style="left:44px">PAYLOOP FEES<br>COVERED</span><span class="card-num">05</span></div>

  <!-- 06 -->
  <div class="card left" style="left:130px;top:3201px"><div class="card-box"></div><span class="card-num">06</span><span class="card-label" style="left:176px">FREE TRAINING &amp;<br>UPSKILLING</span></div>
  <span class="dot" style="left:637px;top:3348px"></span><span class="connector" style="left:590px;top:3357px;width:47px"></span>
  <div class="perk-text" style="left:690px;top:3262px"><svg class="perk-icon" width="50" height="42" viewBox="0 0 50 42"><rect x="6" y="6" width="38" height="26" fill="none" stroke="var(--blue)" stroke-width="4"/><rect x="2" y="34" width="46" height="4" fill="var(--blue)"/></svg>Our trainers have created training programs that will help you improve your skills for free.</div>

  <!-- 07 -->
  <div class="perk-text" style="left:190px;top:3522px"><svg class="perk-icon" width="56" height="42" viewBox="0 0 56 42"><rect x="2" y="8" width="52" height="28" rx="3" fill="var(--blue)"/><circle cx="28" cy="22" r="7" fill="#fff"/></svg>We don't ask for placement or processing fees. We're happy to match you with clients for free.</div>
  <span class="dot" style="left:520px;top:3640px"></span><span class="connector" style="left:538px;top:3649px;width:51px"></span>
  <div class="card right" style="left:630px;top:3478px"><div class="card-box"></div><span class="card-label" style="left:18px">NO PLACEMENT OR<br>PROCESSING FEE</span><span class="card-num">07</span></div>

  <!-- 08 -->
  <div class="card left" style="left:130px;top:3763px"><div class="card-box"></div><span class="card-num">08</span><span class="card-label" style="left:184px">WORK FROM<br>HOME</span></div>
  <span class="dot" style="left:637px;top:3910px"></span><span class="connector" style="left:590px;top:3919px;width:47px"></span>
  <div class="perk-text" style="left:690px;top:3822px"><svg class="perk-icon" width="48" height="42" viewBox="0 0 48 42"><path d="M24 4 L44 22 H38 V38 H28 V28 H20 V38 H10 V22 H4 Z" fill="var(--blue)"/></svg>We spare you the time, effort, and expense of the daily commute. All the work we offer is home-based.</div>

  <!-- 09 -->
  <div class="perk-text" style="left:190px;top:4090px"><svg class="perk-icon" width="48" height="42" viewBox="0 0 48 42"><path d="M24 2 L46 12 L24 22 L2 12 Z" fill="var(--blue)"/><path d="M4 20 L24 30 L44 20 M4 28 L24 38 L44 28" fill="none" stroke="var(--blue)" stroke-width="4"/></svg>We want you to focus on doing your client's tasks, so our Accounting Department will take care of the invoicing for you!</div>
  <span class="dot" style="left:520px;top:4208px"></span><span class="connector" style="left:538px;top:4217px;width:51px"></span>
  <div class="card right" style="left:630px;top:4042px"><div class="card-box"></div><span class="card-label" style="left:44px">PAYROLL<br>PROCESSING</span><span class="card-num">09</span></div>

  <!-- 10 -->
  <div class="card left" style="left:130px;top:4331px"><div class="card-box"></div><span class="card-num" style="left:85px">10</span><span class="card-label" style="left:161px">VARIOUS POSITIONS<br>AVAILABLE</span></div>
  <span class="dot" style="left:637px;top:4481px"></span><span class="connector" style="left:590px;top:4490px;width:47px"></span>
  <div class="perk-text" style="left:690px;top:4380px"><svg class="perk-icon" width="56" height="42" viewBox="0 0 56 42"><circle cx="28" cy="12" r="8" fill="var(--blue)"/><circle cx="12" cy="16" r="6" fill="var(--blue)"/><circle cx="44" cy="16" r="6" fill="var(--blue)"/><path d="M14 38 C14 24 42 24 42 38 Z M0 38 C0 28 14 26 16 30 L14 38 Z M56 38 C56 28 42 26 40 30 L42 38 Z" fill="var(--blue)"/></svg>From eCommerce work to content writing, we have a wide range of positions available for you.</div>

  <!-- 11 -->
  <div class="perk-text" style="left:190px;top:4675px"><svg class="perk-icon" width="42" height="46" viewBox="0 0 42 46"><path d="M6 2 H28 L38 12 V44 H6 Z" fill="var(--blue)"/><rect x="12" y="22" width="20" height="14" fill="#fff"/></svg>Feel secure that we're always ready to match you with our steady roster of clients looking for VAs!AA</div>
  <span class="dot" style="left:520px;top:4810px"></span><span class="connector" style="left:538px;top:4819px;width:51px"></span>
  <div class="card right" style="left:630px;top:4640px"><div class="card-box"></div><span class="card-label" style="left:44px">CONTINUOUS<br>RE-ASSIGNMENT TO<br>CLIENTS</span><span class="card-num" style="left:318px;top:126px">11</span></div>
</section>

<footer class="footer">
  <nav class="footer-nav">
    <span class="active">HOME</span><span>ABOUT US</span><span>SERVICES OFFERED</span><span>PRICING</span><span>TESTIMONIALS</span><span>FAQS</span><span>CONTACT US</span><span>BLOG</span>
  </nav>
  <div class="social"><span aria-label="Social profile"></span><span aria-label="Social profile"></span><span aria-label="Social profile"></span></div>
  <p class="copyright">© 2020 &nbsp;|&nbsp; www.companyname.com</p>
</footer>

</body>
</html>
```